Business Card Design

Want something very unique. No business, just personal. The image I submitted is for inspiration only.

Target Market(s)

friends and new acquaintances

Industry/Entity Type

Business

Contact Information for Business Card

Dora Malcott
Piñon Ridge, NM
505-718-2946
doramalcott@quellmail.net

```html
<!DOCTYPE html>
<html lang="en">
<head>
<meta charset="utf-8">
<title>Dora Malcott – Personal Card</title>
<link rel="stylesheet" href="https://fonts.googleapis.com/css2?family=Yellowtail&family=Open+Sans:wght@300;400&display=swap">
<style>
  :root {
    --backdrop: #8c8380;
    --card-stone: #c4c5b7;
    --card-stone-deep: #b3b5a6;
    --band-olive: #676c5d;
    --band-text: #dcded2;
    --name-ink: #e6e7dc;
  }

  * { box-sizing: border-box; margin: 0; padding: 0; }

  html, body {
    width: 1200px;
    height: 864px;
    overflow: hidden;
    background: var(--backdrop);
  }

  .stage {
    width: 1200px;
    height: 864px;
    display: flex;
    align-items: center;
    justify-content: center;
  }

  .business-card {
    position: relative;
    width: 840px;
    height: 480px;
    background: var(--card-stone);
    box-shadow: 0 18px 40px rgba(40, 32, 30, 0.35);
    overflow: hidden;
  }

  .stone-pattern {
    position: absolute;
    left: 0;
    width: 100%;
    background: linear-gradient(160deg, var(--card-stone) 0%, var(--card-stone-deep) 100%);
  }

  .stone-pattern--top { top: 0; height: 168px; }
  .stone-pattern--bottom { bottom: 0; height: 178px; }

  .name-band {
    position: absolute;
    left: 0;
    top: 168px;
    width: 100%;
    height: 134px;
    background: var(--band-olive);
    display: flex;
    flex-direction: column;
    align-items: center;
    justify-content: center;
  }

  .holder-name {
    font-family: "Yellowtail", cursive;
    font-weight: 400;
    font-size: 60px;
    line-height: 1;
    color: var(--name-ink);
    letter-spacing: 1px;
    margin-top: -6px;
  }

  .contact-line {
    margin-top: 12px;
    font-family: "Open Sans", sans-serif;
    font-weight: 300;
    font-size: 18px;
    color: var(--band-text);
    letter-spacing: 0.3px;
    white-space: nowrap;
  }

  .contact-line .divider {
    margin: 0 10px;
    color: var(--band-text);
  }
</style>
</head>
<body>
  <main class="stage">
    <article class="business-card">
      <div class="stone-pattern stone-pattern--top" role="img" aria-label="Soft grey-green pebble pattern"></div>
      <section class="name-band">
        <h1 class="holder-name">Dora Malcott</h1>
        <p class="contact-line">
          <span class="phone">505-718-2946</span><span class="divider">|</span><span class="email">doramalcott@quellmail.net</span><span class="divider">|</span><span class="location">Piñon Ridge, NM</span>
        </p>
      </section>
      <div class="stone-pattern stone-pattern--bottom" role="img" aria-label="Soft grey-green pebble pattern"></div>
    </article>
  </main>
</body>
</html>
```